Stationery Design Project for Marketing Consultancy

I have started a new consultancy business and require the following elements to be designed using existing logo:
• Business card
• Letterhead
• Envelope (DL, C4, C5)
• Microsoft word template for report writing
• A4 Presentation Folder
• Powerpoint template
COPY FOR FRONT AND BACK OF BUSINESS CARD
logo
'Measurable Marketing. Epic Results' slogan (but no need to use existing lockup with logo)
name, B Bus. Mktg, Grad Dip Digital Mktg, CPM (post nominal abbreviations in smaller font)
mobile: 04XX-XXX-XXX (I will give details to the winner to add)
website: www.tolvarin.com.au
email: info@tolvarin.com.au
COPY FOR LETTERHEAD
Logo
Company Name
Please, submit your designs that include business card, letterhead and envelope. Once selected the winner will be asked to complete the project by creating the rest of the artwork.
FINAL FILES
Print ready files to be supplied as well as Indesign files so that minor amends can be made if necessary in future.
• Layered vectors in EPS & PDF
• Screen quality JPEG & PNGs
ABOUT THE BUSINESS: TOLVARIN
I work with clients to understand their business challenges, developing and executing measurable marketing strategies tied to key business metrics. Services include:
Services include:
• Business planning and business development
• Marketing and brand strategy
• Insight-driven integrated campaigns
• Loyalty programs and retention marketing
• Marketing automation
• Direct marketing (traditional and digital)
• Content strategy and development
Hi everyone,
Target Market(s)
Corporate decision makers (heads of marketing, general managers etc) and small to medium sized business owners. Predominately male aged 35+
Industry/Entity Type
Marketing
Requirements
Must have
- BRAND PERSONALITY
The successful design will communicate brand personality. I am a professional, results-driven entrepreneur, but want to show off my creative flair.
MEMORABILITY
Looking for a unique and eye-catching design. Am considering special printing effects (die cuts, letterpress, interactive elements, embossing, foiling etc) or a striking minimalist approach.
Nice to have
- I have a mission that could be incorporated on reverse if room -
Turning insights into actions & passion into profit.
Should not have
- Use of pink or green.

```html
<!DOCTYPE html>
<html lang="en">
<head>
<meta charset="utf-8">
<title>Tolvarin Stationery</title>
<link rel="stylesheet" href="https://fonts.googleapis.com/css2?family=Open+Sans:wght@400;600;700&display=swap">
<style>
  :root {
    --backdrop: #c9cbce;
    --ink: #000000;
    --paper: #ffffff;
    --mark: #d9d9d9;
    --text-dark: #111111;
  }
  html, body {
    margin: 0;
    padding: 0;
    overflow: hidden;
  }
  body {
    width: 1200px;
    height: 885px;
    background: var(--backdrop);
    position: relative;
    font-family: "Open Sans", Arial, sans-serif;
    color: var(--text-dark);
  }
  .sheet {
    position: absolute;
    background: var(--paper);
    overflow: hidden;
  }
  .brand {
    display: flex;
    flex-direction: column;
    align-items: center;
    color: var(--mark);
  }
  .brand-dot {
    border-radius: 50%;
    background: var(--mark);
  }
  .brand-name {
    font-weight: 700;
    letter-spacing: 0.02em;
    line-height: 1;
  }
  .brand-tagline {
    font-weight: 600;
    line-height: 1.2;
    white-space: nowrap;
  }
  .contact {
    position: absolute;
    font-size: 5px;
    line-height: 1.5;
  }
  .contact strong {
    font-weight: 700;
    font-size: 5.5px;
  }
  .web {
    position: absolute;
    font-size: 5px;
    font-weight: 700;
  }

  /* Business cards */
  .card {
    top: 180px;
    width: 115px;
    height: 77px;
    background: var(--ink);
  }
  .card-front { left: 259px; }
  .card-front .brand { margin-top: 20px; }
  .card-front .brand-dot { width: 14px; height: 14px; margin-bottom: 5px; }
  .card-front .brand-name { font-size: 10px; }
  .card-front .brand-tagline { font-size: 3.6px; margin-top: 2px; }
  .card-back { left: 390px; top: 181px; }
  .card-back .brand { position: absolute; right: 6px; top: 6px; }
  .card-back .brand-dot { width: 7px; height: 7px; margin-bottom: 2px; }
  .card-back .brand-name { font-size: 5px; }
  .card-back .brand-tagline { font-size: 2px; }
  .card-back .contact { left: 24px; top: 25px; color: var(--paper); }

  /* Envelope */
  .envelope {
    left: 616px;
    top: 135px;
    width: 337px;
    height: 159px;
  }
  .envelope-flap {
    position: absolute;
    left: 0;
    top: 0;
    width: 165px;
    height: 159px;
    background: var(--ink);
  }
  .envelope-flap .brand { margin-top: 32px; }
  .envelope-flap .brand-dot { width: 12px; height: 12px; margin-bottom: 4px; }
  .envelope-flap .brand-name { font-size: 9px; }
  .envelope-flap .brand-tagline { font-size: 3px; margin-top: 1px; }
  .envelope-window {
    position: absolute;
    left: 13px;
    top: 77px;
    width: 124px;
    height: 45px;
    background: var(--paper);
    border-radius: 5px;
  }
  .envelope .contact { left: 184px; top: 129px; }
  .envelope .web { right: 20px; top: 145px; font-weight: 400; }

  /* Letterhead */
  .letterhead {
    left: 233px;
    top: 318px;
    width: 316px;
    height: 425px;
  }
  .letterhead-band {
    height: 50px;
    background: var(--ink);
  }
  .letterhead-band .brand { padding-top: 5px; }
  .letterhead-band .brand-dot { width: 12px; height: 12px; margin-bottom: 3px; }
  .letterhead-band .brand-name { font-size: 8.5px; }
  .letterhead-band .brand-tagline { font-size: 3px; margin-top: 1px; }
  .letterhead .contact { left: 12px; top: 395px; }
  .letterhead .web { right: 12px; top: 409px; }

  /* Presentation folder */
  .folder {
    left: 607px;
    top: 321px;
    width: 346px;
    height: 444px;
  }
  .folder-band {
    position: absolute;
    left: 0;
    top: 91px;
    width: 100%;
    height: 228px;
    background: var(--ink);
  }
  .folder-band .brand { margin-top: 62px; }
  .folder-band .brand-dot { width: 34px; height: 34px; margin-bottom: 14px; }
  .folder-band .brand-name { font-size: 30px; }
  .folder-band .brand-tagline { font-size: 9.5px; margin-top: 6px; }
  .folder .web { left: 0; width: 100%; text-align: center; top: 417px; }
</style>
</head>
<body>

  <section class="sheet card card-front" aria-label="Business card front">
    <div class="brand">
      <span class="brand-dot"></span>
      <span class="brand-name">TOLVARIN</span>
      <span class="brand-tagline">SHARPER STRATEGY. PROVEN GROWTH.</span>
    </div>
  </section>

  <section class="sheet card card-back" aria-label="Business card back">
    <div class="brand">
      <span class="brand-dot"></span>
      <span class="brand-name">TOLVARIN</span>
      <span class="brand-tagline">SHARPER STRATEGY. PROVEN GROWTH.</span>
    </div>
    <div class="contact">
      <strong>Company Name</strong><br>
      M: xxx xxx xxxx<br>
      E: info@tolvarin.com.au<br>
      <strong>www.tolvarin.com.au</strong>
    </div>
  </section>

  <section class="sheet envelope" aria-label="DL envelope">
    <div class="envelope-flap">
      <div class="brand">
        <span class="brand-dot"></span>
        <span class="brand-name">TOLVARIN</span>
        <span class="brand-tagline">SHARPER STRATEGY. PROVEN GROWTH.</span>
      </div>
      <div class="envelope-window"></div>
    </div>
    <div class="contact">
      <strong>Company Name</strong><br>
      M: xxx xxx xxxx<br>
      E: info@tolvarin.com.au
    </div>
    <div class="web">www.tolvarin.com.au</div>
  </section>

  <section class="sheet letterhead" aria-label="Letterhead">
    <header class="letterhead-band">
      <div class="brand">
        <span class="brand-dot"></span>
        <span class="brand-name">TOLVARIN</span>
        <span class="brand-tagline">SHARPER STRATEGY. PROVEN GROWTH.</span>
      </div>
    </header>
    <div class="contact">
      <strong>Company Name</strong><br>
      M: xxx xxx xxxx<br>
      E: info@tolvarin.com.au
    </div>
    <div class="web">www.tolvarin.com.au</div>
  </section>

  <section class="sheet folder" aria-label="A4 presentation folder">
    <div class="folder-band">
      <div class="brand">
        <span class="brand-dot"></span>
        <span class="brand-name">TOLVARIN</span>
        <span class="brand-tagline">SHARPER STRATEGY. PROVEN GROWTH.</span>
      </div>
    </div>
    <div class="web">www.tolvarin.com.au</div>
  </section>

</body>
</html>
```